Brightmere Peace Trust

We need web design for an anti-gun violence campaign that will urge people to ring bells instead of shooting guns to bring in the New Year and whenever someone is killed by gun violence.
This campaign will raise funds for social agencies that help communities with social issues to help especially youth with no place to turn, play or dream. Also will fund New Gun Laws policies. Should be global in aspect but appealing to United States first.
Find poem by Lord Edmund Brackwell "Sing Larks, Swift Larks" as our theme on google.
This is a start up and nothing else to give. But need something eye catching for appeal of campaign.

Target Market(s)

Universal , more male oriented.

Industry/Entity Type

Gun

Number of Pages Required

1 page

Other font styles liked:
• Designers Can Choose

Requirements
Must have
• Strong imagery and vivid colors and bell of course.
Nice to have
• A stand out design beyond words that hit home. See attached file for website ideas

```html
<!DOCTYPE html>
<html lang="en">
<head>
<meta charset="utf-8">
<title>Brightmere Peace Trust</title>
<link href="https://fonts.googleapis.com/css2?family=Lato:ital,wght@0,300;0,400;0,700;1,300;1,400&family=Merriweather:wght@400;700&display=swap" rel="stylesheet">
<style>
:root{
  --red:#cc0000;
  --red-dark:#a80000;
  --red-button:#e01010;
  --page:#ebebeb;
  --panel:#f3f3f3;
  --white:#ffffff;
  --ink:#222222;
  --muted:#6b6b6b;
  --footer:#151515;
  --footer-text:#dddddd;
}
*{margin:0;padding:0;box-sizing:border-box}
html,body{width:1006px;height:1200px;overflow:hidden}
body{position:relative;background:var(--page);font-family:'Lato',sans-serif;color:var(--ink)}
.abs{position:absolute}

.site-header{left:0;top:0;width:1006px;height:64px;background:var(--red)}
.brand{left:53px;top:20px;font-family:'Merriweather',serif;font-size:18px;color:var(--white);letter-spacing:.2px}
.main-nav{right:0;top:0;height:64px;display:flex}
.main-nav a{display:block;height:64px;line-height:72px;padding:0 15px;color:var(--white);text-decoration:none;font-size:11.5px;text-transform:uppercase;letter-spacing:.1px}
.main-nav a.active{background:var(--red-dark)}

.hero{left:0;top:64px;width:1006px;height:342px}
.hero-photo{position:absolute;inset:0;background:linear-gradient(180deg,#3a2418 0%,#8a4a22 38%,#b06a2e 52%,#2a140a 72%,#5a2c14 86%,#2a1208 100%)}
.hero-quote{position:absolute;left:0;right:0;top:80px;text-align:center;color:var(--white);font-weight:400;font-size:37px;line-height:43px}
.hero-author{position:absolute;left:0;right:0;top:222px;text-align:center;color:var(--white);font-style:italic;font-weight:300;font-size:12px}
.slider-dots{position:absolute;left:478px;top:308px;display:flex;gap:9px}
.slider-dots span{width:10px;height:10px;border:1px solid var(--white);border-radius:50%;position:relative}
.slider-dots span.on::after{content:"";position:absolute;left:2px;top:2px;width:4px;height:4px;background:var(--white);border-radius:50%}

.feature{top:435px;width:437px;height:194px;background:var(--white);padding:7px}
.feature-photo{position:absolute;left:7px;top:7px;right:7px;bottom:7px}
.feature-left{left:54px}
.feature-left .feature-photo{background:linear-gradient(90deg,#2a2a2e 0%,#56565a 30%,#5c5a5a 100%)}
.feature-right{left:514px}
.feature-right .feature-photo{background:linear-gradient(90deg,#0e1410 0%,#1a2a20 45%,#4a4038 70%,#141414 100%)}
.feature-body{position:absolute;top:38px;color:var(--white)}
.feature-title{font-family:'Merriweather',serif;font-size:19px;font-weight:400;margin-bottom:14px}
.feature-text{font-size:10.5px;line-height:17px;width:190px}
.btn-small{display:inline-block;margin-top:26px;background:var(--red-button);color:var(--white);font-size:10px;padding:0 13px;height:34px;line-height:34px;border:1px solid #ff4a4a;border-radius:2px;text-decoration:none}
.feature-left .feature-body{left:208px}
.feature-right .feature-body{left:23px}

.donation{left:54px;top:662px;width:898px;height:132px;background:var(--panel);border-left:5px solid var(--red)}
.donation-title{position:absolute;left:25px;top:36px;font-family:'Merriweather',serif;font-size:22px;font-weight:700;color:var(--red);letter-spacing:.3px}
.donation-text{position:absolute;left:24px;top:72px;font-style:italic;font-size:13.5px;color:#333}
.donation-photo{position:absolute;left:435px;top:0;width:166px;height:132px;background:radial-gradient(ellipse at 50% 55%,#e8b89a 0%,#d39a7a 45%,#f3f3f3 75%)}
.btn-donate{position:absolute;left:698px;top:34px;width:137px;height:54px;line-height:54px;text-align:center;background:var(--red-button);color:var(--white);font-weight:700;font-size:13.5px;letter-spacing:.3px;border-radius:2px;box-shadow:0 1px 3px rgba(0,0,0,.3)}

.column{top:824px;width:276px}
.column-photo{height:151px;background:var(--white);padding:7px;box-shadow:0 0 2px rgba(0,0,0,.06)}
.column-photo div{width:100%;height:100%}
.col-about{left:54px}
.col-about .column-photo div{background:linear-gradient(135deg,#7a3a2a 0%,#c08a6a 45%,#6a8a3a 100%)}
.col-involved{left:365px}
.col-involved .column-photo div{background:linear-gradient(180deg,#c8e0b0 0%,#d6e8c0 60%,#e8eee0 100%)}
.col-event{left:677px}
.col-event .column-photo div{background:linear-gradient(180deg,#3a5a6a 0%,#8ab0b8 55%,#d6d8b8 100%)}
.column-title{margin-top:16px;font-family:'Merriweather',serif;font-size:18px;font-weight:400;color:var(--red);text-transform:uppercase}
.column-text{margin-top:11px;font-size:10.5px;line-height:17px;color:var(--muted)}

.site-footer{left:0;top:1102px;width:1006px;height:98px;background:var(--footer)}
.footer-nav{position:absolute;left:54px;top:37px;display:flex;gap:25px}
.footer-nav a{color:var(--footer-text);text-decoration:none;font-size:9px;text-transform:uppercase}
.copyright{position:absolute;left:54px;top:60px;font-size:8.5px;color:var(--footer-text)}
.social{position:absolute;left:830px;top:38px;display:flex;gap:16px}
.social span{width:12px;height:12px;border-radius:50%;background:var(--footer-text)}
</style>
</head>
<body>

<header class="site-header abs">
  <div class="brand abs">BRIGHTMERE PEACE TRUST</div>
  <nav class="main-nav abs">
    <a class="active" href="#">Home</a>
    <a href="#">About Gun Violence</a>
    <a href="#">Get Involved</a>
    <a href="#">Donate</a>
    <a href="#">Events</a>
    <a href="#">Contact</a>
  </nav>
</header>

<section class="hero abs">
  <div class="hero-photo" role="img" aria-label="Sunset over a lake with dark hills and a soaring bird"></div>
  <p class="hero-quote">Sing out, swift larks, to the open sky,<br>The drifting cloud, the early light<br>The year is fading in the night</p>
  <p class="hero-author">-Lord Edmund Brackwell-</p>
  <div class="slider-dots"><span></span><span class="on"></span><span></span></div>
</section>

<article class="feature feature-left abs">
  <div class="feature-photo" role="img" aria-label="Person holding a handgun behind their back"></div>
  <div class="feature-body">
    <h2 class="feature-title">ANTI-GUN VIOLENCE</h2>
    <p class="feature-text">All your funds goes to New Gun Laws policies Campaign</p>
    <a class="btn-small" href="#">READ MORE</a>
  </div>
</article>

<article class="feature feature-right abs">
  <div class="feature-photo" role="img" aria-label="Woman holding a remote control in a dark room"></div>
  <div class="feature-body">
    <h2 class="feature-title">THE TALK PROJECT</h2>
    <p class="feature-text">All your funds goes to New Gun Laws policies Campaign</p>
    <a class="btn-small" href="#">READ MORE</a>
  </div>
</article>

<section class="donation abs">
  <h2 class="donation-title">MAKE A DONATION</h2>
  <p class="donation-text">All your funds goes to New Gun Laws policies Campaign</p>
  <div class="donation-photo" role="img" aria-label="Open hands cradling a paper cut-out family"></div>
  <div class="btn-donate">DONATE NOW</div>
</section>

<section class="column col-about abs">
  <div class="column-photo"><div role="img" aria-label="Many hands stacked together"></div></div>
  <h3 class="column-title">About&nbsp; Us</h3>
  <p class="column-text">Sed ut perspiciatis unde omnis iste natus error sit volupta-tem accusantium doloremque laudantium, totam rem aperiam,</p>
</section>

<section class="column col-involved abs">
  <div class="column-photo"><div role="img" aria-label="Child holding a pinwheel against a pale sky"></div></div>
  <h3 class="column-title">Get Involved</h3>
  <p class="column-text">Sed ut perspiciatis unde omnis iste natus error sit volupta-tem accusantium doloremque laudantium, totam rem aperiam,</p>
</section>

<section class="column col-event abs">
  <div class="column-photo"><div role="img" aria-label="Hands forming a heart shape against the sky"></div></div>
  <h3 class="column-title">Latest Event</h3>
  <p class="column-text">Sed ut perspiciatis unde omnis iste natus error sit volupta-tem accusantium doloremque laudantium, totam rem aperiam,</p>
</section>

<footer class="site-footer abs">
  <nav class="footer-nav">
    <a href="#">Home</a>
    <a href="#">About Gun Violence</a>
    <a href="#">Get Involved</a>
    <a href="#">Donate</a>
    <a href="#">Events</a>
    <a href="#">Contact</a>
  </nav>
  <p class="copyright">©2014 BRIGHTMERE PEACE TRUST.</p>
  <div class="social" aria-label="Social links">
    <span></span><span></span><span></span><span></span><span></span>
  </div>
</footer>

</body>
</html>
```